Cleaning service website design

We need a new nice web design(logo will be the same) for a new cleaning service Company:

Informations about Company and logo you can take from flyers in attachments.

This is a cleaning service Company which have simple rules and we would like to show that(in checklist form) on website:

- What we do and that we're Cleaning Green

- Why us?

- How much(our pricing is simple)

Also we would like to communicate with clients by some nice/big pictures on website and the most important thing is our phone number and short/fast Brimtallow.

Also there should be some space for description about our Company.

Generally all information on main page can be short: about us, about service(what we do), last reviews, tips (for example: Tip of the week) and other can be some introduction to subpage where will be more information.

There will be few subpages like: About us, About our service, Photos(Before and after), Reviews , Tips, FAQ, Contact, Looking for a Job? - most of them will be just text so you can project just one example.

```html
<!DOCTYPE html>
<html lang="en">
<head>
<meta charset="utf-8">
<title>Tidy Nest House Cleaning</title>
<link rel="stylesheet" href="https://fonts.googleapis.com/css2?family=PT+Sans:ital,wght@0,400;0,700;1,400&family=PT+Sans+Narrow:wght@700&display=swap">
<style>
:root{
  --green:#6aae1f;
  --green-dark:#3f8a12;
  --leaf:#7cc22c;
  --blue:#1f62b0;
  --ink:#222;
  --text:#333;
  --muted:#888;
  --line:#d6d6d6;
  --orange-top:#ffb11a;
  --orange-bot:#ff7a00;
  --red:#e01010;
  --white:#fff;
}
*{box-sizing:border-box;margin:0;padding:0}
html,body{width:1200px;height:1035px;overflow:hidden;background:var(--white)}
body{font-family:"PT Sans",sans-serif;color:var(--text);position:relative}

.site-header{position:absolute;left:0;top:0;width:1200px;height:134px;background:var(--white)}
.site-header::after{content:"";position:absolute;left:0;right:0;top:127px;height:7px;background:linear-gradient(#e2e2e2,#f7f7f7)}
.brand{position:absolute;left:150px;top:38px;display:flex;align-items:center;gap:10px}
.brand-dot{width:34px;height:34px;border-radius:50%;background:var(--green)}
.brand-name{font-size:28px;font-weight:700;color:var(--green-dark);line-height:1}
.brand-sub{position:absolute;left:194px;top:76px;font-size:11px;font-weight:700;color:var(--blue)}
.call{position:absolute;right:150px;top:13px;text-align:right}
.call-line{font-size:14px;color:var(--ink)}
.call-line b{font-weight:700}
.call-number{display:flex;align-items:center;justify-content:flex-end;gap:6px;font-size:27px;font-weight:700;color:var(--ink);line-height:1.15}
.main-nav{position:absolute;right:148px;top:66px;height:61px;display:flex}
.main-nav a{display:flex;align-items:center;padding:0 16px;font-family:"PT Sans Narrow",sans-serif;font-size:13px;font-weight:700;color:#2b2b2b;text-decoration:none;text-transform:uppercase}
.main-nav a.current{background:#f0f0f0;color:var(--green);border-bottom:4px solid var(--leaf);padding-top:4px}

.hero{position:absolute;left:0;top:134px;width:1200px;height:503px;overflow:hidden}
.hero-photo{position:absolute;inset:0;background:
  radial-gradient(ellipse at 45% 35%,#dfe9d8 0%,#a9c49a 22%,transparent 50%),
  radial-gradient(ellipse at 80% 55%,#b8b56a 0%,#8e9a48 20%,transparent 42%),
  linear-gradient(90deg,#34521f 0%,#5d7d3d 25%,#7f9a64 45%,#4f7a2c 70%,#2f5a18 100%)}
.hero-copy{position:absolute;left:150px;top:52px;color:var(--white);text-shadow:0 1px 3px rgba(0,0,0,.45)}
.hero-title{font-size:41px;font-weight:400;letter-spacing:.5px;line-height:1}
.hero-title b{font-weight:700}
.hero-sub{margin-top:12px;font-size:23px;font-weight:700}
.hero-sub .price{font-size:40px;color:var(--red);text-shadow:0 1px 0 #fff,0 2px 3px rgba(0,0,0,.4)}
.perks{list-style:none;margin-top:8px}
.perks li{display:flex;align-items:center;gap:13px;height:33.5px;font-size:15px;font-weight:700}
.badge{position:absolute;left:312px;top:273px;width:70px;height:70px;border-radius:50%;background:radial-gradient(circle at 50% 70%,#8fd13a,#4f9d1c 60%,#f4f4f4 62%);box-shadow:0 2px 5px rgba(0,0,0,.35)}
.cta{position:absolute;left:149px;top:376px;width:247px;height:57px;border-radius:4px;background:linear-gradient(var(--orange-top),var(--orange-bot));display:flex;align-items:center;justify-content:center;gap:12px;color:var(--white);font-size:27px;font-weight:700;text-decoration:none;text-shadow:0 1px 2px rgba(0,0,0,.3)}

.card{position:absolute;top:674px;width:288px;height:341px;border:1px solid var(--line);background:#fbfbfb}
.card::after{content:"";position:absolute;left:12px;right:12px;bottom:-10px;height:10px;background:radial-gradient(ellipse at top,rgba(0,0,0,.18),transparent 70%)}
.card-photo{margin:4px 4px 0;height:109px}
.card-photo.family{background:linear-gradient(120deg,#d9c2a0,#efe2cf 40%,#c9b6a0 70%,#8a7560)}
.card-photo.pricing{background:linear-gradient(120deg,#e9e2d6,#cfc2b0 40%,#b9a994 70%,#eee)}
.card h2{text-align:center;font-size:21px;font-weight:400;color:var(--green);margin-top:10px}
.ticks{list-style:none;margin:14px 0 0 22px;font-size:14px}
.ticks li{display:flex;gap:9px;margin-bottom:9px;line-height:1.35}
.ticks svg{flex:none;margin-top:2px}
.prices{list-style:none;margin:17px 0 0 34px;font-size:14.5px}
.prices li{margin-bottom:10px}
.prices b{font-weight:400;color:var(--green-dark)}
.price-note{margin:6px 0 0 37px;font-size:14px;line-height:1.25}
.price-note a{color:var(--blue)}
.price-fine{margin:14px 0 0 39px;font-size:12px;font-style:italic}
.estimate h2{margin-top:18px}
.field{display:block;margin:0 0 13px 31px;width:225px;height:29px;border:1px solid var(--line);background:var(--white);padding-left:11px;font:11px "PT Sans",sans-serif;color:var(--muted);line-height:27px}
.field-row{display:flex;gap:8px;margin-left:31px}
.field-row .field{margin:0;width:108px}
.estimate form{margin-top:14px}
.estimate-foot{display:flex;justify-content:space-between;align-items:flex-start;margin:28px 31px 0 32px}
.foot-label{font-size:11px;font-weight:700;color:var(--ink)}
.foot-number{font-size:19px;font-weight:700;color:var(--blue);line-height:1}
.submit{width:82px;height:27px;border:0;border-radius:2px;background:linear-gradient(var(--orange-top),var(--orange-bot));color:var(--white);font:700 13px "PT Sans",sans-serif}
</style>
</head>
<body>

<header class="site-header">
  <div class="brand"><span class="brand-dot"></span><span class="brand-name">Tidy Nest</span></div>
  <div class="brand-sub">House Cleaning</div>
  <div class="call">
    <div class="call-line"><b>Call Us</b> to arrange your cleaning on</div>
    <div class="call-number">
      <svg width="16" height="22" viewBox="0 0 16 22"><path d="M4 1 L7 1 L8 6 L5.5 7.5 Q6 13 10 16 L12 14 L15.5 17 L14 21 Q4 20 1.5 9 Q1 4 4 1Z" fill="#1f62b0"/></svg>
      555-014-2736
    </div>
  </div>
  <nav class="main-nav">
    <a class="current" href="#">Home</a>
    <a href="#">About Us</a>
    <a href="#">Our Services</a>
    <a href="#">Photos</a>
    <a href="#">Reviews</a>
    <a href="#">Tips</a>
    <a href="#">Careers</a>
    <a href="#">FAQ</a>
    <a href="#">Contact</a>
  </nav>
</header>

<section class="hero">
  <div class="hero-photo" role="img" aria-label="Woman with outstretched arms breathing fresh air in a misty green forest"></div>
  <div class="hero-copy">
    <h1 class="hero-title">SIMPLIFY <b>YOUR LIFE</b></h1>
    <p class="hero-sub">and some there House Cleaning from <span class="price">$79</span></p>
    <ul class="perks">
      <li><svg width="22" height="24" viewBox="0 0 22 24"><path d="M2 22 Q2 6 21 1 Q20 18 2 22Z" fill="#7cc22c"/></svg>Locally Owned &amp; Operated</li>
      <li><svg width="22" height="24" viewBox="0 0 22 24"><path d="M2 22 Q2 6 21 1 Q20 18 2 22Z" fill="#7cc22c"/></svg>Reliable &amp; Affordable</li>
      <li><svg width="22" height="24" viewBox="0 0 22 24"><path d="M2 22 Q2 6 21 1 Q20 18 2 22Z" fill="#7cc22c"/></svg>All Supplies Provided</li>
      <li><svg width="22" height="24" viewBox="0 0 22 24"><path d="M2 22 Q2 6 21 1 Q20 18 2 22Z" fill="#7cc22c"/></svg>No Contracts</li>
      <li><svg width="22" height="24" viewBox="0 0 22 24"><path d="M2 22 Q2 6 21 1 Q20 18 2 22Z" fill="#7cc22c"/></svg>Pet Friendly</li>
      <li><svg width="22" height="24" viewBox="0 0 22 24"><path d="M2 22 Q2 6 21 1 Q20 18 2 22Z" fill="#7cc22c"/></svg>Green Cleaning</li>
    </ul>
    <span class="badge"></span>
  </div>
  <a class="cta" href="#">GET STARTED
    <svg width="30" height="26" viewBox="0 0 30 26"><path d="M0 8 H15 V1 L29 13 L15 25 V18 H0Z" fill="#fff"/></svg>
  </a>
</section>

<section class="card" style="left:148px">
  <div class="card-photo family" role="img" aria-label="Smiling family with their dog on a sofa"></div>
  <h2>What do we clean?</h2>
  <ul class="ticks">
    <li><svg width="18" height="16" viewBox="0 0 18 16"><rect x="1" y="2" width="13" height="13" fill="none" stroke="#6aae1f" stroke-width="1.5"/><path d="M4 8 L7.5 12 L17 1" fill="none" stroke="#3f8a12" stroke-width="2.5"/></svg>Thoroughly clean your bathrooms,<br>kitchen, bedrooms and living areas</li>
    <li><svg width="18" height="16" viewBox="0 0 18 16"><rect x="1" y="2" width="13" height="13" fill="none" stroke="#6aae1f" stroke-width="1.5"/><path d="M4 8 L7.5 12 L17 1" fill="none" stroke="#3f8a12" stroke-width="2.5"/></svg>Mop or vacuum your floors</li>
    <li><svg width="18" height="16" viewBox="0 0 18 16"><rect x="1" y="2" width="13" height="13" fill="none" stroke="#6aae1f" stroke-width="1.5"/><path d="M4 8 L7.5 12 L17 1" fill="none" stroke="#3f8a12" stroke-width="2.5"/></svg>Dust surfaces</li>
    <li><svg width="18" height="16" viewBox="0 0 18 16"><rect x="1" y="2" width="13" height="13" fill="none" stroke="#6aae1f" stroke-width="1.5"/><path d="M4 8 L7.5 12 L17 1" fill="none" stroke="#3f8a12" stroke-width="2.5"/></svg>Collect garbage</li>
    <li><svg width="18" height="16" viewBox="0 0 18 16"><rect x="1" y="2" width="13" height="13" fill="none" stroke="#6aae1f" stroke-width="1.5"/><path d="M4 8 L7.5 12 L17 1" fill="none" stroke="#3f8a12" stroke-width="2.5"/></svg>Make beds</li>
  </ul>
</section>

<section class="card" style="left:455px">
  <div class="card-photo pricing" role="img" aria-label="Family looking at a laptop together"></div>
  <h2>Pricing is..simple</h2>
  <ul class="prices">
    <li><b>$79</b> for homes less than 1000 sq ft</li>
    <li><b>$89</b> for homes 1000-1800 sq ft</li>
    <li><b>$99</b> for homes 1800-2600 sq ft</li>
  </ul>
  <p class="price-note">If your home is larger than 2600 sq ft<br>please <a href="#">call for a quote</a></p>
  <p class="price-fine">*rates are for regular service*</p>
</section>

<section class="card estimate" style="left:762px">
  <h2>Quick Free Estimate</h2>
  <form>
    <span class="field">Name</span>
    <span class="field">E-mail</span>
    <span class="field">Postal Code</span>
    <span class="field">Phone</span>
    <div class="field-row"><span class="field">No. of Bathrooms</span><span class="field">No. of Bedrooms</span></div>
    <div class="estimate-foot">
      <div><div class="foot-label">CALL US TODAY</div><div class="foot-number">555-014-2736</div></div>
      <button class="submit" type="button">SUBMIT</button>
    </div>
  </form>
</section>

</body>
</html>
```